Travel Agency Website - Simple General

Need a 7 page simple design that is pretty repetitive. Need to be able to load quickly that is SEO optimized. Trying to give ideas on what they can do, be personal as we are local, but at the same time come across as professional and get information easily with little burden.

- Landing Page
- Brimwell Vacations Page
- Family Trips
- Road Trips from Texas
- Other Destinations
- About Us Page
- Contact Us Page

Target Market(s)

Families

Coding

Coded - Design and coding required

Number of Pages Required

5+ page

Colors

Designer to choose colors to be used in the design.

Requirements
Must have
• Like it to flow easily with our logo. Use that for colors, etc.

```html
<!DOCTYPE html>
<html lang="en">
<head>
<meta charset="utf-8">
<title>Roam Together Travel Co. — Family Travel Planning</title>
<link href="https://fonts.googleapis.com/css2?family=Poppins:wght@300;400;500;600;700&display=swap" rel="stylesheet">
<style>
:root{
  --teal:#2f8a86;
  --teal-dark:#1b5b66;
  --ink:#1e2a2e;
  --muted:#4a5659;
  --sky-top:#d6e7e8;
  --panel:#e2e9ea;
  --panel-tint:#d5dfe1;
  --white:#ffffff;
}
*{margin:0;padding:0;box-sizing:border-box}
html,body{width:698px;height:1200px;overflow:hidden}
body{font-family:"Poppins",sans-serif;color:var(--ink);position:relative;
  background:linear-gradient(180deg,var(--sky-top) 0,#eef4f4 260px,var(--white) 360px,var(--white) 1000px,#eef3f4 1065px)}
.abs{position:absolute}
/* header */
.brand{left:64px;top:16px;display:flex;align-items:center;gap:6px;color:var(--teal-dark);font-weight:600;font-size:12px;line-height:1.1}
.brand .dot{width:22px;height:22px;border-radius:50%;border:2px solid var(--teal-dark)}
.nav{left:193px;top:35px;display:flex;gap:12px;font-size:9px;color:var(--ink);white-space:nowrap}
.nav .active{color:var(--teal-dark);font-weight:600}
/* hero */
.hero-title{left:64px;top:114px;font-size:23.5px;font-weight:300;line-height:27px}
.hero-title strong{display:block;font-weight:700;color:var(--teal);font-size:24px;line-height:28px}
.hero-text{left:64px;top:208px;width:280px;font-size:9px;line-height:15px;color:var(--muted);text-align:justify}
.btn{display:inline-block;background:var(--teal-dark);color:var(--white);font-size:9px;font-weight:500;padding:5px 8px;border-radius:5px;white-space:nowrap}
.btn-light{background:#dbe6e7;color:var(--teal-dark)}
.hero-photo{left:395px;top:78px;width:240px;height:240px;border-radius:50%;
  background:linear-gradient(180deg,#1ec6e6 0,#4fd0e6 30%,#b8893f 55%,#8a7a5a 75%,#6b6f72 100%);
  box-shadow:0 10px 14px -6px rgba(0,0,0,.25)}
/* adventures */
.sec-title{left:0;width:698px;top:374px;text-align:center;font-size:20px;font-weight:300}
.sec-title strong{font-weight:700;color:var(--teal)}
.sec-text{left:110px;width:478px;top:410px;text-align:center;font-size:9px;line-height:15px;color:var(--muted)}
.card{width:148px;height:152px;border:2px solid var(--teal-dark);border-radius:12px;overflow:hidden}
.card .label{position:absolute;left:0;right:0;bottom:18px;text-align:center;color:var(--white);font-size:10px;font-weight:500;text-shadow:0 1px 3px rgba(0,0,0,.5)}
.c1{left:62px;top:470px;transform:rotate(6deg);background:linear-gradient(180deg,#6f7d96 0,#e7a46e 30%,#2d3440 55%,#1c222b 100%)}
.c2{left:204px;top:490px;transform:rotate(-8deg);background:linear-gradient(180deg,#c9dbe8 0,#9db8cf 35%,#6d5a4c 70%,#3b3f45 100%)}
.c3{left:352px;top:469px;transform:rotate(3deg);background:linear-gradient(180deg,#6ea4cf 0,#b9cadb 35%,#a6845c 55%,#3f3c3a 100%)}
.c4{left:490px;top:490px;transform:rotate(-8deg);background:linear-gradient(180deg,#e6ecee 0,#b86a52 40%,#7c6a5d 70%,#3b3a3a 100%)}
/* welcome */
.panel{left:32px;top:711px;width:636px;height:302px;border-radius:24px;background:var(--panel)}
.welcome-photo{left:66px;top:748px;width:276px;height:228px;border-radius:40% 30% 35% 45%;
  background:radial-gradient(circle at 55% 45%,#e8d3c0 0,#c7b9a6 30%,#5c6266 65%,#2b2f33 100%)}
.welcome-title{left:356px;top:746px;font-size:19.5px;font-weight:300;line-height:24px}
.welcome-title strong{display:block;font-weight:700;color:var(--teal);font-size:20px}
.welcome-lead{left:356px;top:804px;width:290px;font-size:9px;line-height:15px;font-weight:500}
.welcome-text{left:356px;top:838px;width:274px;font-size:7.6px;line-height:14px;color:var(--muted);text-align:justify;font-weight:300}
.welcome-text p+p{margin-top:10px}
.suitcase{left:560px;top:948px;width:58px;height:50px;border-radius:10px;background:linear-gradient(180deg,var(--panel) 0,var(--panel-tint) 100%)}
/* footer */
.footer{left:0;top:1065px;width:698px;height:135px;background:var(--teal-dark);color:var(--white)}
.footer .brand{left:64px;top:40px;color:var(--white)}
.footer .brand .dot{border-color:var(--white)}
.contact{right:62px;top:30px;font-size:8.5px;display:flex;gap:8px;align-items:center}
.contact svg{vertical-align:-1px;margin-right:3px}
.fnav{right:64px;top:47px;display:flex;gap:14px;font-size:9.5px;white-space:nowrap}
.fnav2{right:64px;top:63px;display:flex;gap:14px;font-size:8.5px}
.rule{left:64px;top:94px;width:570px;height:1px;background:rgba(255,255,255,.35)}
.copy{left:64px;top:110px;font-size:8px}
.social{right:64px;top:108px;display:flex;gap:3px}
.social span{width:13px;height:13px;border:1px solid var(--white);border-radius:2px}
</style>
</head>
<body>
<header>
  <div class="abs brand"><span class="dot"></span><span>Roam<br>Together</span></div>
  <nav class="abs nav">
    <span class="active">Home</span><span>Brimwell Vacations</span><span>Family Trips</span><span>Road Trips from Texas</span><span>Other Destinations</span><span>More ▾</span>
  </nav>
</header>

<section>
  <h1 class="abs hero-title">Creating Magical Family<br>Adventures —<strong>One Journey at a Time</strong></h1>
  <p class="abs hero-text">From unforgettable Brimwell vacations to scenic Texas road trips and bucket-list family getaways, we help families travel with ease, excitement, and lasting memories.</p>
  <div class="abs" style="left:65px;top:267px;display:flex;gap:7px">
    <span class="btn">Start Planning Your Trip</span>
    <span class="btn btn-light">◉ Explore Destinations</span>
  </div>
  <div class="abs hero-photo" role="img" aria-label="Desert highway leading toward a mountain under a bright blue sky"></div>
  <svg class="abs" style="left:395px;top:78px" width="240" height="240"><circle cx="120" cy="120" r="112" fill="none" stroke="#fff" stroke-width="1.5" stroke-dasharray="6 4"/></svg>
</section>

<section>
  <h2 class="abs sec-title">Explore Our Favorite <strong>Adventures</strong></h2>
  <p class="abs sec-text">Lorem ipsum dolor sit amet, consectetur adipiscing elit, sed do eiusmod tempor incididunt ut labore et dolore magna aliqua. Ut enim ad minim veniam, quis nostrud exercitation</p>
  <div class="abs card c1" role="img" aria-label="Seaside pier with a lit ferris wheel at sunset"><span class="label">Brimwell Vacations</span></div>
  <div class="abs card c2" role="img" aria-label="Happy family playing together outdoors"><span class="label">Family Trips</span></div>
  <div class="abs card c3" role="img" aria-label="Straight desert road toward mountains"><span class="label">Texas Road Trips</span></div>
  <div class="abs card c4" role="img" aria-label="Couple reading a map in front of a brick arch"><span class="label">Other Destinations</span></div>
</section>

<section>
  <div class="abs panel"></div>
  <div class="abs welcome-photo" role="img" aria-label="Smiling traveller reading a folded map, framed by a brush stroke"></div>
  <h2 class="abs welcome-title">Welcome To<strong>Roam Together</strong></h2>
  <p class="abs welcome-lead">At Roam Together Travel Co., we believe the best memories are made together.</p>
  <div class="abs welcome-text">
    <p>Whether you're dreaming of magical castle moments, cross-country adventures, relaxing beach escapes, or scenic road trips across Texas, we're here to help make every journey stress-free and unforgettable. We specialize in family-focused travel planning designed around your unique style, budget, and travel dreams.</p>
    <p>From the first idea to the final itinerary, we handle the details so you can focus on making memories.</p>
  </div>
  <span class="abs btn" style="left:356px;top:953px">Start Planning Your Trip</span>
  <div class="abs suitcase" role="img" aria-label="Line drawing of a rolling suitcase"></div>
</section>

<footer class="abs footer">
  <div class="abs brand"><span class="dot"></span><span>Roam<br>Together</span></div>
  <div class="abs contact">
    <span><svg width="8" height="8" viewBox="0 0 10 10"><path d="M2 0 L4 2 L3 4 Q4 6 6 7 L8 6 L10 8 L8 10 Q2 9 0 2 Z" fill="#fff"/></svg>555.010.0199</span>
    <span>/</span>
    <span><svg width="9" height="7" viewBox="0 0 10 8"><rect width="10" height="8" rx="1" fill="#fff"/><path d="M0 1 L5 5 L10 1" fill="none" stroke="#1b5b66"/></svg>hello@roamtogethertravel.com</span>
  </div>
  <nav class="abs fnav"><span>Home</span><span>Brimwell Vacations</span><span>Family Trips</span><span>Road Trips from Texas</span><span>Other Destinations</span></nav>
  <nav class="abs fnav2"><span>About Us</span><span>Contact Us</span></nav>
  <div class="abs rule"></div>
  <p class="abs copy">© 2026 Roam Together. All rights reserved.</p>
  <div class="abs social"><span></span><span></span></div>
</footer>
</body>
</html>
```